Retail Jewelry Business Card Design Project

We are in need of a new business card design for a retail jewelry store. This store is in the business of fine jewelry including but not specific to bridal jewelry, diamonds, designer jewelry and watches.

This store has been in business for 20 years but continues to strive for a modern professional appeal. The main colors use for this business are a royal blue, white and silver.

Target Market(s)

Target market is ages 18-50

Industry/Entity Type

Jewelry

Requirements
Must have
• Sales Person Name
Sales Person Email Address

Store Address
Store Phone
Website

Standard business card size. No odd shapes or sizes.
Nice to have
• Overall modern feel for card.

We have thought that a design with a nice feature of the logo on the back of the card would be nice but open to ideas.
Should not have
• No specific images of jewelry should be used.

```html
<!DOCTYPE html>
<html lang="en">
<head>
<meta charset="utf-8">
<title>Harlan Reed Fine Jewelry – Business Card</title>
<link rel="stylesheet" href="https://fonts.googleapis.com/css2?family=Jost:wght@400;500;600&display=swap">
<style>
  :root {
    --royal: #2e3a8f;
    --lavender: #7d7bc2;
    --white: #ffffff;
    --ink: #1f2560;
    --stage: #e9e9ee;
    --shadow: rgba(20, 24, 60, 0.18);
  }
  * { margin: 0; padding: 0; box-sizing: border-box; }
  html, body {
    width: 1200px; height: 750px; overflow: hidden;
    background: var(--stage);
    font-family: "Jost", Arial, sans-serif;
  }
  .canvas {
    position: relative; width: 1200px; height: 750px;
    display: flex; align-items: center; justify-content: center; gap: 60px;
  }
  .card {
    position: relative; width: 520px; height: 297px;
    box-shadow: 0 8px 24px var(--shadow);
    overflow: hidden;
  }
  .brand { font-weight: 500; line-height: 1; }
  .brand__name { display: block; font-size: 46px; letter-spacing: 0.5px; }
  .brand__rule { display: block; height: 2px; margin-top: 6px; }
  .brand__tag { display: block; font-size: 17px; letter-spacing: 3px; text-transform: uppercase; margin-top: 6px; }

  /* Front */
  .card--front { background: var(--white); color: var(--ink); }
  .card__waves { position: absolute; inset: 0; width: 100%; height: 100%; }
  .card--front .brand {
    position: absolute; left: 54px; top: 26px; width: 290px; color: var(--royal);
  }
  .card--front .brand__rule { background: var(--lavender); }
  .card--front .brand__tag { padding-left: 40px; }
  .address {
    position: absolute; left: 62px; top: 134px;
    font-size: 12.5px; color: var(--ink);
  }
  .contact-list {
    position: absolute; left: 62px; top: 160px; list-style: none;
    font-size: 12.5px; color: var(--ink);
  }
  .contact-list li { display: flex; align-items: center; gap: 7px; height: 19px; }
  .contact-list svg { width: 10px; height: 10px; fill: var(--royal); flex: none; }
  .person {
    position: absolute; right: 24px; top: 248px;
    color: var(--white); font-weight: 600; font-size: 16px;
  }

  /* Back */
  .card--back { background: var(--royal); color: var(--white); }
  .card--back .brand {
    position: absolute; left: 110px; right: 110px; top: 78px; text-align: center;
  }
  .card--back .brand__name { font-size: 54px; }
  .card--back .brand__rule { background: var(--white); }
  .card--back .brand__tag { font-size: 20px; margin-top: 8px; }
  .website {
    position: absolute; left: 0; right: 0; top: 226px; text-align: center;
    font-size: 13px; letter-spacing: 3px;
  }
</style>
</head>
<body>
<main class="canvas">
  <section class="card card--front" aria-label="Business card front">
    <svg class="card__waves" viewBox="0 0 520 297" preserveAspectRatio="none" aria-hidden="true">
      <path d="M0 258 C250 258 410 228 520 128 L520 297 L0 297 Z" fill="var(--lavender)"/>
      <path d="M0 265 C255 264 415 234 520 139 L520 297 L0 297 Z" fill="var(--white)"/>
      <path d="M0 272 C260 270 420 240 520 150 L520 297 L0 297 Z" fill="var(--royal)"/>
    </svg>
    <div class="brand">
      <span class="brand__name">Harlan Reed</span>
      <span class="brand__rule"></span>
      <span class="brand__tag">Fine Jewelry</span>
    </div>
    <p class="address">2280 Marlowe Street, Bayport, FL 32999</p>
    <ul class="contact-list">
      <li><svg viewBox="0 0 10 10"><path d="M2 0.5 L3.6 2.6 L2.7 3.7 C3.3 5 4.6 6.4 6 7 L7.1 6.1 L9.5 7.6 L8.6 9.4 C4.6 9.2 0.8 5.4 0.6 1.4 Z"/></svg>555-010-2468</li>
      <li><svg viewBox="0 0 10 10"><path d="M0.5 2 H9.5 V8.5 H0.5 Z M1.2 2.6 L5 5.6 L8.8 2.6" stroke="var(--white)" stroke-width="0.6"/></svg>harlan@harlanreedjewelry.com</li>
      <li><svg viewBox="0 0 10 10"><circle cx="5" cy="5" r="4.5"/><path d="M0.5 5 H9.5 M5 0.5 V9.5 M5 0.5 C2.5 3 2.5 7 5 9.5 M5 0.5 C7.5 3 7.5 7 5 9.5" fill="none" stroke="var(--white)" stroke-width="0.6"/></svg>www.harlanreedjewelry.com</li>
    </ul>
    <p class="person">Harlan Reed Whitmore</p>
  </section>

  <section class="card card--back" aria-label="Business card back">
    <div class="brand">
      <span class="brand__name">Harlan Reed</span>
      <span class="brand__rule"></span>
      <span class="brand__tag">Fine Jewelry</span>
    </div>
    <p class="website">www.harlanreedjewelry.com</p>
  </section>
</main>
</body>
</html>
```